Card design for orthopaedic surgeons working as The Brightwater Joint Centre

Business cards, letterhead

Colors

Designer to choose colors to be used in the design.

Requirements
Must have
• Late addition.
• Cards letterhead must have logos of
• Crestmoor Lindell College of Surgeons
• Varenwood Bone Health Association
Nice to have
• Back of card to have space for appointment time to be added by hand and some blank space for writing incidental other notes.

```html
<!DOCTYPE html>
<html lang="en">
<head>
<meta charset="utf-8">
<title>The Brightwater Joint Centre – Business Card</title>
<link href="https://fonts.googleapis.com/css2?family=Montserrat:wght@400&family=Open+Sans:wght@400;700&display=swap" rel="stylesheet">
<style>
  :root {
    --backdrop: #2a2b2e;
    --card-white: #ffffff;
    --brand-blue: #35aef5;
    --brand-navy: #13314d;
    --ink-dark: #222a33;
    --text-light: #ffffff;
  }
  * { margin: 0; padding: 0; box-sizing: border-box; }
  html, body {
    width: 1200px; height: 960px; overflow: hidden;
    background: var(--backdrop);
  }
  .canvas {
    width: 1200px; height: 960px;
    display: flex; flex-direction: column; align-items: center; justify-content: center;
    gap: 60px;
  }
  .card {
    width: 700px; height: 400px;
    background: var(--card-white);
    position: relative; overflow: hidden;
  }

  /* Front */
  .card-front {
    display: flex; flex-direction: column; align-items: center;
    padding-top: 150px; gap: 60px;
  }
  .brand-name {
    font-family: "Montserrat", sans-serif; font-weight: 400;
    color: var(--brand-blue);
    font-size: 31px; letter-spacing: -0.6px; white-space: nowrap;
  }
  .front-url {
    font-family: "Open Sans", sans-serif; font-size: 18px;
    letter-spacing: 6px; color: var(--ink-dark);
  }
  .front-url .domain { color: var(--brand-blue); }

  /* Back */
  .back-logo-panel {
    position: absolute; left: 0; top: 0; bottom: 0; width: 60%;
    padding: 128px 0 0 26px;
  }
  .back-logo-panel .brand-name { font-size: 24px; }
  .back-divider {
    position: absolute; left: 60%; top: 0; bottom: 0; width: 7px;
    background: var(--brand-navy);
  }
  .back-divider::before {
    content: ""; position: absolute; left: -12px; top: 54px;
    border-top: 10px solid transparent; border-bottom: 10px solid transparent;
    border-right: 12px solid var(--brand-navy);
  }
  .back-details {
    position: absolute; left: calc(60% + 7px); right: 0; top: 0; bottom: 0;
    background: var(--brand-blue); color: var(--text-light);
    font-family: "Open Sans", sans-serif;
    padding: 46px 16px 0 22px;
  }
  .person-name { font-family: Arial, "Open Sans", sans-serif; font-weight: 700; font-size: 23px; line-height: 1.1; }
  .person-title { font-family: Arial, "Open Sans", sans-serif; font-size: 17px; margin-bottom: 26px; }
  .address { font-size: 16px; line-height: 1.35; margin-bottom: 14px; }
  .contact-list { list-style: none; font-size: 16px; line-height: 1.55; }
  .contact-list li { display: flex; align-items: center; gap: 10px; white-space: nowrap; }
  .contact-list svg { width: 13px; height: 13px; flex: none; }
</style>
</head>
<body>
<main class="canvas">
  <section class="card card-front" aria-label="Business card front">
    <div class="brand-name">The Brightwater Joint Centre</div>
    <div class="front-url">www.<span class="domain">brightwaterjoint</span>.com</div>
  </section>

  <section class="card card-back" aria-label="Business card back">
    <div class="back-logo-panel">
      <div class="brand-name">The Brightwater Joint Centre</div>
    </div>
    <div class="back-divider"></div>
    <div class="back-details">
      <div class="person-name">Mara Ellison</div>
      <div class="person-title">Title</div>
      <div class="address">Street Name, City Name<br>Zipcode - 012345</div>
      <ul class="contact-list">
        <li>
          <svg viewBox="0 0 16 16" aria-hidden="true"><path fill="#fff" d="M3.5 1l2.5 3-1.5 1.8c.8 1.9 2.3 3.4 4.2 4.2L10.5 8.5l3 2.5-1.4 2.8C7 13.5 2.5 9 2.2 3.9z"/></svg>
          <span>012-345-6789</span>
        </li>
        <li>
          <svg viewBox="0 0 16 16" aria-hidden="true"><rect x="1" y="3.5" width="14" height="9" rx="1" fill="#fff"/><path d="M1.5 4l6.5 5 6.5-5" stroke="#35aef5" stroke-width="1.4" fill="none"/></svg>
          <span>info@brightwaterjoint.com</span>
        </li>
        <li>
          <svg viewBox="0 0 16 16" aria-hidden="true" fill="none" stroke="#fff" stroke-width="1.3"><circle cx="8" cy="8" r="6.5"/><ellipse cx="8" cy="8" rx="2.8" ry="6.5"/><path d="M1.5 8h13M2.5 4.8h11M2.5 11.2h11"/></svg>
          <span>www.brightwaterjoint.com</span>
        </li>
      </ul>
    </div>
  </section>
</main>
</body>
</html>
```